Sophisticated, clean website reflecting my feminine, playful side to sell my abstract art,

I need a website no more than 3 pages to showcase my paintings, a little about me and some contact info. I do abstracts so looking for something a little edgy, yet feminine and current.
Updates

Hi there, These are some artists websites that I Iike: Marnelvoss.com (I like how airy it is) peterwallombry.com garethpolvens.com (I like how it scrolls) I'll need a place for a photo ( a headshot-i do not have it yet so I'll need to be able to upload that later) as well as an area for my bio. Also, it's important that I will be able to upload any new photos and descriptions easily so it should be user friendly. Lastly, I like in a sunny place so would like to have this seem upbeat and playful as that is how i like to paint. thanks-I'm trying to upload my photos now -

Target Market(s)

ppl ages 35-70 who want large scale art for their homes

Industry/Entity Type

art

Coding

Coded - Design and coding required

Number of Pages Required

3 page

Colors

Designer to choose colors to be used in the design.

Requirements
Must have
• photos of my art, a place for my bio, be easy to reach me. tasteful-nothing too "in your face" -my clients are pretty high end and organized. They like clean lines
Nice to have
• sophisticated background, muted tones in the back-similar clean font throughout-no cursive
Should not have
• too many dark areas. Too many blocks of color. Too serious.

```html
<!DOCTYPE html>
<html lang="en">
<head>
<meta charset="utf-8">
<title>Lena Marwick — Abstract Art</title>
<link href="https://fonts.googleapis.com/css2?family=Questrial&family=Mulish:wght@300;400&display=swap" rel="stylesheet">
<style>
  :root {
    --ink: #3a3a3c;
    --ink-soft: #4a4a4d;
    --rule: #c9c9cb;
    --underline: #a9a9ab;
    --frame: #9a9a9c;
    --page-top: #ffffff;
    --page-bottom: #f0f0f1;
    --hero-pink: #c99aa8;
    --hero-rust: #a25a3c;
    --hero-cream: #e6c9b4;
    --art-teal: #1f8a8a;
    --art-orange: #c8651f;
    --art-cream: #ddd6c8;
  }
  * { margin: 0; padding: 0; box-sizing: border-box; }
  html, body { width: 1200px; height: 3019px; overflow: hidden; }
  body {
    position: relative;
    font-family: "Mulish", sans-serif;
    color: var(--ink);
    background: linear-gradient(to bottom, var(--page-top) 0, var(--page-top) 1420px, var(--page-bottom) 2200px, var(--page-bottom) 100%);
  }
  .site-header { position: absolute; top: 0; left: 0; width: 1200px; height: 131px; border-bottom: 2px solid var(--rule); background: var(--page-top); }
  .brand { position: absolute; top: 42px; left: 0; width: 1200px; display: flex; justify-content: center; align-items: center; gap: 18px;
    font-family: "Questrial", sans-serif; font-weight: 400; font-size: 56px; letter-spacing: 2px; color: var(--ink-soft); line-height: 1; }
  .brand-mark { width: 30px; height: 46px; background: var(--ink-soft); }
  .main-nav { position: absolute; top: 131px; left: 0; width: 1200px; height: 59px; display: flex; justify-content: center; align-items: center;
    font-family: "Questrial", sans-serif; font-size: 18px; color: var(--ink); background: var(--page-top); }
  .main-nav a { color: inherit; text-decoration: none; }
  .nav-dot { width: 4px; height: 4px; background: #9b9b9d; margin: 0 56px; }
  .hero { position: absolute; top: 190px; left: 0; width: 1200px; height: 658px;
    background: radial-gradient(circle at 55% 58%, #6e3a2e 0, var(--hero-rust) 12%, var(--hero-pink) 34%, var(--hero-cream) 60%, #b47a6a 85%, #8b5a4a 100%); }
  .hero-arrow { position: absolute; top: 469px; }
  .section-title { position: absolute; left: 0; width: 1200px; text-align: center; font-family: "Questrial", sans-serif; font-weight: 400; font-size: 52px; color: var(--ink-soft); letter-spacing: 1px; line-height: 1; }
  .section-title span { display: inline-block; padding: 0 4px 6px; border-bottom: 4px solid var(--underline); }
  .about-title { top: 980px; }
  .portrait-frame { position: absolute; left: 101px; top: 1090px; width: 312px; height: 354px; border: 2px solid var(--frame); padding: 6px; background: #fff; }
  .portrait { width: 100%; height: 100%; background: linear-gradient(to bottom, #f3f3f3 0%, #eeeeee 55%, #fafafa 100%); }
  .bio { position: absolute; left: 465px; top: 1092px; width: 640px; font-weight: 300; font-size: 18.5px; line-height: 30.8px; color: var(--ink); }
  .bio p + p { margin-top: 15px; }
  .gallery-title { top: 1620px; }
  .gallery-frame { position: absolute; left: 151px; top: 1718px; width: 892px; height: 559px; border: 2px solid var(--frame); padding: 10px; background: #f4f4f4; }
  .artwork { width: 100%; height: 100%;
    background: linear-gradient(120deg, var(--art-cream) 0%, var(--art-orange) 22%, var(--art-teal) 42%, #1c3c55 55%, var(--art-orange) 70%, var(--art-cream) 88%, #c7a84a 100%); }
  .gallery-arrow { position: absolute; top: 1963px; }
  .contact-title { top: 2423px; }
  .contact-lede { position: absolute; top: 2502px; left: 0; width: 1200px; text-align: center; font-weight: 300; font-size: 21px; color: var(--ink); }
  .contact-item { position: absolute; width: 320px; text-align: center; font-family: "Questrial", sans-serif; font-size: 16.5px; color: var(--ink); letter-spacing: 0.2px; }
  .contact-item svg { display: block; margin: 0 auto 14px; }
  .social-dot { width: 36px; height: 36px; border: 2px solid var(--ink); border-radius: 50%; margin: 0 auto 14px; }
  .site-footer { position: absolute; top: 2941px; left: 0; width: 1200px; height: 78px; border-top: 1px solid var(--rule);
    text-align: center; padding-top: 24px; font-size: 14px; font-weight: 400; color: var(--ink-soft); }
</style>
</head>
<body>
  <header class="site-header">
    <div class="brand"><span>LENA</span><span class="brand-mark"></span><span>MARWICK</span></div>
  </header>
  <nav class="main-nav">
    <a href="#home">HOME</a><span class="nav-dot"></span>
    <a href="#about">ABOUT ME</a><span class="nav-dot"></span>
    <a href="#gallery">GALLERY</a><span class="nav-dot"></span>
    <a href="#contact">CONTACT</a>
  </nav>

  <section class="hero" id="home" role="img" aria-label="Abstract painting of a rose in pink, rust and cream brushstrokes">
  </section>
  <svg class="hero-arrow" style="left:22px" width="28" height="48" viewBox="0 0 28 48"><polyline points="24,4 4,24 24,44" fill="none" stroke="#fff" stroke-width="3"/></svg>
  <svg class="hero-arrow" style="left:1136px" width="28" height="48" viewBox="0 0 28 48"><polyline points="4,4 24,24 4,44" fill="none" stroke="#fff" stroke-width="3"/></svg>

  <h2 class="section-title about-title" id="about"><span>ABOUT ME</span></h2>
  <div class="portrait-frame"><div class="portrait" role="img" aria-label="Artist headshot placeholder"></div></div>
  <div class="bio">
    <p>Lorem ipsum dolor sit amet, consectetur adipiscing elit, sed do eiusmod tempor incididunt ut labore et dolore magna aliqua. Ut enim ad minim veniam, quis nostrud exercitation Lorem ipsum dolor sit amet, consectetur adipiscing elit, sed do eiusmod tempor incididunt ut labore et dolore</p>
    <p>Duis aute irure dolor in reprehenderit in voluptate velit esse cillum dolore eu fugiat nulla pariatur. Excepteur sint occaecat cupidatat non proident, sunt in culpa qui officia deserunt mollit anim id est laborum.</p>
    <p>Sed ut perspiciatis unde pariatur. Excepteur sint occaecat cupidatat non proi-dent, sunt in culpa qui officia deserunt mollit anim id est laborum.didunt ut labore et dolore Duis aute irure dolor in reprehenderit in voluptate</p>
  </div>

  <h2 class="section-title gallery-title" id="gallery"><span>GALLERY</span></h2>
  <svg class="gallery-arrow" style="left:86px" width="28" height="48" viewBox="0 0 28 48"><polyline points="24,4 4,24 24,44" fill="none" stroke="#6a6a6c" stroke-width="3.5"/></svg>
  <div class="gallery-frame"><div class="artwork" role="img" aria-label="Abstract painting in teal, orange, black and cream brushstrokes"></div></div>
  <svg class="gallery-arrow" style="left:1086px" width="28" height="48" viewBox="0 0 28 48"><polyline points="4,4 24,24 4,44" fill="none" stroke="#6a6a6c" stroke-width="3.5"/></svg>

  <h2 class="section-title contact-title" id="contact"><span>CONTACT ME</span></h2>
  <p class="contact-lede">Please get in touch with me on below details.</p>

  <div class="contact-item" style="left:264px; top:2612px;">
    <svg width="42" height="30" viewBox="0 0 42 30"><rect x="1" y="1" width="40" height="28" fill="none" stroke="#3a3a3c" stroke-width="1.6"/><polyline points="1,1 21,17 41,1" fill="none" stroke="#3a3a3c" stroke-width="1.6"/><line x1="1" y1="29" x2="16" y2="13" stroke="#3a3a3c" stroke-width="1.6"/><line x1="41" y1="29" x2="26" y2="13" stroke="#3a3a3c" stroke-width="1.6"/></svg>
    INFO@LENAMARWICK.COM
  </div>
  <div class="contact-item" style="left:633px; top:2602px;">
    <svg width="42" height="42" viewBox="0 0 42 42"><path d="M10 4 L16 12 L12 17 C14 23 19 28 25 30 L30 26 L38 32 L34 39 C20 38 5 24 3 9 Z" fill="none" stroke="#3a3a3c" stroke-width="1.6" stroke-linejoin="round"/><path d="M24 8 A10 10 0 0 1 34 18" fill="none" stroke="#3a3a3c" stroke-width="1.6"/><path d="M24 2 A16 16 0 0 1 40 18" fill="none" stroke="#3a3a3c" stroke-width="1.6"/></svg>
    PHONE: (555) 014 2270
  </div>
  <div class="contact-item" style="left:268px; top:2752px;">
    <div class="social-dot"></div>
    SNAPFOLIO @LMARWICKART
  </div>
  <div class="contact-item" style="left:638px; top:2746px;">
    <div class="social-dot"></div>
    CLIPWAVE @LMPAINTER
  </div>

  <footer class="site-footer">© 2022 Lena Marwick &nbsp; All Rights Reserved</footer>
</body>
</html>
```